Marwick Law Letterhead

We need a new letterhead design for a Law Firm. The address for the law firm is 1475 Calloway Street, Suite 210, Houston, Texas 77041. Phone Number: 832-361-9027; Fax Number: 832-614-7359. The logo is uploaded to the project.

```html
<!DOCTYPE html>
<html lang="en">
<head>
<meta charset="utf-8">
<title>Marwick Law Letterhead</title>
<link rel="stylesheet" href="https://fonts.googleapis.com/css2?family=Libre+Baskerville:wght@400;700&display=swap">
<style>
  :root {
    --backdrop: #e7e4e0;
    --paper: #ffffff;
    --sidebar: #f2f2f2;
    --navy: #1c2f64;
    --red: #b3191f;
    --ink: #1f2a4d;
  }
  html, body {
    margin: 0;
    width: 1200px;
    height: 900px;
    overflow: hidden;
    background: var(--backdrop);
  }
  .letterhead {
    position: absolute;
    left: 270px;
    top: 24px;
    width: 660px;
    height: 852px;
    background: var(--paper);
    box-shadow: 0 6px 18px rgba(0,0,0,0.18);
    font-family: "Libre Baskerville", Georgia, serif;
  }
  .sidebar {
    position: absolute;
    left: 22px;
    top: 0;
    width: 236px;
    height: 852px;
    background: var(--sidebar);
  }
  .brand {
    position: absolute;
    left: 18px;
    top: 40px;
    width: 200px;
    text-align: center;
  }
  .brand-name {
    margin: 0;
    font-size: 24px;
    line-height: 30px;
    font-weight: 400;
    color: var(--navy);
    letter-spacing: 0.5px;
  }
  .brand-tagline {
    margin: 8px 0 0;
    font-size: 5px;
    line-height: 7px;
    letter-spacing: 0.6px;
    color: var(--red);
    text-transform: uppercase;
  }
  .contact {
    position: absolute;
    left: 12px;
    top: 740px;
    color: var(--ink);
    font-size: 9px;
    font-weight: 700;
    letter-spacing: 0.6px;
  }
  .contact-line {
    display: flex;
    align-items: center;
    gap: 5px;
    height: 12px;
    margin-bottom: 8px;
  }
  .contact-line svg { width: 10px; height: 10px; fill: var(--red); }
  .address {
    margin: 10px 0 0;
    line-height: 13px;
  }
  .rule-red {
    position: absolute;
    left: 0;
    top: 829px;
    width: 236px;
    height: 4px;
    background: var(--red);
  }
  .band-navy {
    position: absolute;
    left: 0;
    top: 836px;
    width: 236px;
    height: 16px;
    background: var(--navy);
  }
</style>
</head>
<body>
  <main class="letterhead">
    <aside class="sidebar">
      <header class="brand">
        <h1 class="brand-name">Marwick Law</h1>
        <p class="brand-tagline">Steady counsel when it matters most</p>
      </header>
      <div class="contact">
        <div class="contact-line">
          <svg viewBox="0 0 24 24" aria-hidden="true"><path d="M6.6 10.8a15.1 15.1 0 0 0 6.6 6.6l2.2-2.2c.3-.3.7-.4 1-.2 1.1.4 2.3.6 3.6.6.6 0 1 .4 1 1V20c0 .6-.4 1-1 1A17 17 0 0 1 3 4c0-.6.4-1 1-1h3.5c.6 0 1 .4 1 1 0 1.3.2 2.5.6 3.6.1.3 0 .7-.2 1z"/></svg>
          <span>832-361-9027</span>
        </div>
        <div class="contact-line">
          <svg viewBox="0 0 24 24" aria-hidden="true"><path d="M6 3h10v5H6zM3 9h18v9h-3v3H6v-3H3zm5 6v4h8v-4z"/></svg>
          <span>832-614-7359</span>
        </div>
        <p class="address">1475 Calloway Street,<br>Suite 210,<br>Houston, Texas 77041</p>
      </div>
      <div class="rule-red"></div>
      <div class="band-navy"></div>
    </aside>
  </main>
</body>
</html>
```